Restaurant Menu New Design

Hello Designers,

Blue Fern is a casual family oriented dine-in restaurant, we serve American Italian dishes like Pizza, Pasta, and Sandwiches.

We are excited about adding some new delicious dishes and recipes to our menu. And we are looking for a talented and creative designer to design it.

The menu is a 12 page black leather book, page size is:
6.5" X 11.69" (16.51 cm X 29.69 cm)

Below is the scope of work and requirements:

1) Design a completely all new, creative, and beautiful menu, including cover page, blue fern oven intro. page, interior pages, and kids menu page.

2) Design a take out edition of the menu. It will be exactly the same as the dine-in menu, but with the addition of a back cover page with info such as contacts, social media, location map, etc…

3) Files are required in Adobe Illustrator format. Layers should be organized, all text should be editable, and all the food pictures easy to change.

4) This is a two language menu, so you are required to make space in the design for a second language. The easiest way to do that is have every item listed in English twice, then I will edit the second text with Illustrator.

5) In your initial design submission, the minimum you are required to submit are these 4 pages:
– Cover page
– Typical interior menu page
– Kids menu page
– Take-out menu back cover page

If your initial design is selected, then you are required to submit all remaining pages to complete the project.

In the link below, you will find:
1) Logo
2) New menu text in Excel
3) Food images (will take some time to upload)
4) The old dine-in and take out menu designs

https://www.filevaultra.com/sh/kq7tmwzabe3pxd/BBBrTnpLk41QaWmZpQ8V2X7Jd?dl=0

Thank you for stopping by and reading this brief. I hope you like this project and enjoy designing our new menu. Please let me know if you have any questions.

Cheers!

Project Deadline Extended
Reason: We have decided to extend the deadline due to the low number of submissions which was much lower than the expected submissions we were give by Brief Harbor.

```html
<!DOCTYPE html>
<html lang="en">
<head>
<meta charset="utf-8">
<title>Blue Fern – Starters Menu Page</title>
<link href="https://fonts.googleapis.com/css2?family=Libre+Baskerville:ital,wght@0,400;0,700;1,400&display=swap" rel="stylesheet">
<style>
  :root {
    --paper: #ffffff;
    --wood-dark: #2f1d12;
    --wood-mid: #4a2e1b;
    --panel-light: #b98446;
    --panel-deep: #8c5a2c;
    --brush: #9b6b3f;
    --gold: #f7d21c;
    --cream: #fff6e6;
    --ink-dark: #2e1a0e;
    --frame: #f47a12;
    --mark: #333333;
    --serif: "Libre Baskerville", Georgia, serif;
  }
  * { margin: 0; padding: 0; box-sizing: border-box; }
  html, body { width: 729px; height: 1200px; overflow: hidden; background: var(--paper); }
  .canvas { position: relative; width: 729px; height: 1200px; overflow: hidden; font-family: var(--serif); }

  .print-marks { position: absolute; inset: 0; }

  .menu-page {
    position: absolute; left: 88px; top: 102px; width: 568px; height: 1022px;
    background: linear-gradient(90deg, var(--wood-mid), var(--wood-dark) 70%, #24160d);
    overflow: hidden;
  }
  .menu-page__panel {
    position: absolute; left: 14px; top: 0; width: 305px; height: 100%;
    background: linear-gradient(180deg, var(--panel-light) 0%, #a87238 55%, var(--panel-deep) 100%);
  }
  .menu-page__brush { position: absolute; left: 0; top: 38px; }
  .menu-page__title {
    position: absolute; left: 48px; top: 52px;
    color: var(--cream); font-weight: 700; font-size: 31px; letter-spacing: 0.5px;
    text-shadow: 1px 2px 2px rgba(0,0,0,0.45);
  }

  .menu-item { position: absolute; left: 40px; width: 245px; }
  .menu-item__name { font-weight: 700; font-size: 13px; line-height: 16px; color: var(--gold); text-transform: uppercase; }
  .menu-item__desc { font-style: italic; font-size: 10.5px; line-height: 16px; color: var(--cream); }
  .menu-item--alt .menu-item__name { color: var(--ink-dark); }
  .menu-item--alt .menu-item__desc { color: var(--ink-dark); }

  .dish { position: absolute; left: 284px; width: 266px; }
  .dish__photo { height: 184px; border: 5px solid var(--frame); }
  .dish__caption { margin-top: 10px; margin-left: 28px; color: var(--cream); font-weight: 700; font-size: 10px; text-transform: uppercase; }
  .dish__photo--pizza { background: radial-gradient(circle at 50% 55%, #e8c58a, #b9803f 60%, #6e3b1d); }
  .dish__photo--milanese { background: radial-gradient(circle at 50% 55%, #f4efe6 0%, #c38445 45%, #6b4a2c 100%); }
  .dish__photo--fries { background: radial-gradient(circle at 50% 45%, #f2a21a, #e5c276 55%, #8a5a2a); }
  .dish__photo--salad { background: radial-gradient(circle at 50% 55%, #7c9a3d, #e9e3d6 55%, #2d2219); }
</style>
</head>
<body>
<div class="canvas">
  <svg class="print-marks" width="729" height="1200" viewBox="0 0 729 1200" aria-hidden="true">
    <g class="color-bar">
      <rect x="172" y="51" width="25" height="24" fill="#fffbb0"/><rect x="197" y="51" width="25" height="24" fill="#fff37a"/><rect x="222" y="51" width="25" height="24" fill="#fff200"/><rect x="247" y="51" width="25" height="24" fill="#fff200"/>
      <rect x="272" y="51" width="25" height="24" fill="#b9e3f0"/><rect x="297" y="51" width="25" height="24" fill="#7fcbe3"/><rect x="322" y="51" width="25" height="24" fill="#3cb3d5"/><rect x="347" y="51" width="25" height="24" fill="#00a0c8"/>
      <rect x="372" y="51" width="25" height="24" fill="#f8b5d4"/><rect x="397" y="51" width="25" height="24" fill="#f37ab3"/><rect x="422" y="51" width="25" height="24" fill="#ee3e93"/><rect x="447" y="51" width="25" height="24" fill="#ec008c"/>
      <rect x="472" y="51" width="25" height="24" fill="#bbbbbb"/><rect x="497" y="51" width="25" height="24" fill="#888888"/><rect x="522" y="51" width="25" height="24" fill="#444444"/><rect x="547" y="51" width="25" height="24" fill="#000000"/>
    </g>
    <use href="#bar-top" />
    <g transform="translate(0,1096)">
      <rect x="172" y="51" width="25" height="24" fill="#fffbb0"/><rect x="197" y="51" width="25" height="24" fill="#fff37a"/><rect x="222" y="51" width="25" height="24" fill="#fff200"/><rect x="247" y="51" width="25" height="24" fill="#fff200"/>
      <rect x="272" y="51" width="25" height="24" fill="#b9e3f0"/><rect x="297" y="51" width="25" height="24" fill="#7fcbe3"/><rect x="322" y="51" width="25" height="24" fill="#3cb3d5"/><rect x="347" y="51" width="25" height="24" fill="#00a0c8"/>
      <rect x="372" y="51" width="25" height="24" fill="#f8b5d4"/><rect x="397" y="51" width="25" height="24" fill="#f37ab3"/><rect x="422" y="51" width="25" height="24" fill="#ee3e93"/><rect x="447" y="51" width="25" height="24" fill="#ec008c"/>
      <rect x="472" y="51" width="25" height="24" fill="#bbbbbb"/><rect x="497" y="51" width="25" height="24" fill="#888888"/><rect x="522" y="51" width="25" height="24" fill="#444444"/><rect x="547" y="51" width="25" height="24" fill="#000000"/>
    </g>
    <defs>
      <linearGradient id="gray-ramp" x1="0" y1="0" x2="0" y2="1">
        <stop offset="0" stop-color="#f2f2f2"/><stop offset="1" stop-color="#000"/>
      </linearGradient>
      <g id="reg">
        <circle r="9" fill="none" stroke="var(--mark)" stroke-width="1"/>
        <line x1="-13" y1="0" x2="13" y2="0" stroke="var(--mark)" stroke-width="1"/>
        <line x1="0" y1="-13" x2="0" y2="13" stroke="var(--mark)" stroke-width="1"/>
      </g>
    </defs>
    <rect x="36" y="368" width="25" height="492" fill="url(#gray-ramp)"/>
    <rect x="677" y="368" width="25" height="492" fill="url(#gray-ramp)"/>
    <use href="#reg" x="143" y="63"/><use href="#reg" x="598" y="63"/>
    <use href="#reg" x="49" y="338"/><use href="#reg" x="690" y="338"/>
    <use href="#reg" x="49" y="891"/><use href="#reg" x="690" y="891"/>
    <use href="#reg" x="143" y="1160"/><use href="#reg" x="598" y="1160"/>
    <g stroke="var(--mark)" stroke-width="1">
      <line x1="88" y1="72" x2="88" y2="95"/><line x1="656" y1="72" x2="656" y2="95"/>
      <line x1="58" y1="102" x2="81" y2="102"/><line x1="663" y1="102" x2="686" y2="102"/>
      <line x1="88" y1="1131" x2="88" y2="1154"/><line x1="656" y1="1131" x2="656" y2="1154"/>
      <line x1="58" y1="1124" x2="81" y2="1124"/><line x1="663" y1="1124" x2="686" y2="1124"/>
    </g>
  </svg>

  <main class="menu-page">
    <div class="menu-page__panel"></div>
    <svg class="menu-page__brush" width="340" height="80" viewBox="0 0 340 80" aria-hidden="true">
      <path d="M0 34 L40 22 L120 14 L250 6 L330 10 L318 30 L335 50 L250 56 L150 62 L60 70 L20 62 L35 50 Z" fill="var(--brush)"/>
    </svg>
    <h1 class="menu-page__title">STARTERS</h1>

    <section class="menu-list">
      <article class="menu-item" style="top:128px"><h2 class="menu-item__name">Chili Cheese Fries</h2><p class="menu-item__desc">French fries, topped with beef chili and melted cheddar cheese &nbsp;19</p></article>
      <article class="menu-item" style="top:200px"><h2 class="menu-item__name">Buffalo Tenders</h2><p class="menu-item__desc">Chicken tenders covered in spicy buffalo sauce, served with ranch dressing &nbsp;24</p></article>
      <article class="menu-item menu-item--alt" style="top:253px"><h2 class="menu-item__name">Buffalo Tenders</h2><p class="menu-item__desc">Chicken tenders covered in spicy buffalo sauce, served with ranch dressing &nbsp;24</p></article>
      <article class="menu-item" style="top:322px"><h2 class="menu-item__name">Mozza Sticks</h2><p class="menu-item__desc">"Crispy fried mozzarella cheese, served with marinara &amp; BBQ sauce &nbsp;15"</p></article>
      <article class="menu-item menu-item--alt" style="top:375px"><h2 class="menu-item__name">Mozza Sticks</h2><p class="menu-item__desc">"Crispy fried mozzarella cheese, served with marinara &amp; BBQ sauce &nbsp;15"</p></article>
      <article class="menu-item" style="top:442px"><h2 class="menu-item__name">Onion Rings &nbsp;15</h2></article>
      <article class="menu-item menu-item--alt" style="top:461px"><h2 class="menu-item__name">Onion Rings &nbsp;15</h2></article>
      <article class="menu-item" style="top:497px"><h2 class="menu-item__name">Chicken Tenders</h2><p class="menu-item__desc">Lightly breaded chicken breast strips, fried &amp; served with honey mustard &amp; BBQ sauce &nbsp;19</p></article>
      <article class="menu-item menu-item--alt" style="top:550px"><h2 class="menu-item__name">Chicken Tenders</h2><p class="menu-item__desc">Lightly breaded chicken breast strips, fried &amp; served with honey mustard &amp; BBQ sauce &nbsp;19</p></article>
      <article class="menu-item" style="top:618px"><h2 class="menu-item__name">Garlic Bread Sticks</h2><p class="menu-item__desc">"Garlic bread sticks served with marinara sauce with mozzarella cheese 13"</p></article>
      <article class="menu-item menu-item--alt" style="top:671px"><h2 class="menu-item__name">Garlic Bread Sticks</h2><p class="menu-item__desc">"Garlic bread sticks served with marinara sauce with mozzarella cheese 13"</p></article>
      <article class="menu-item" style="top:740px"><h2 class="menu-item__name">Starter Sampler</h2><p class="menu-item__desc">Includes Mozza Sticks, Chicken Tenders, Onion Rings, and Chili Cheese Fries &nbsp;38</p></article>
      <article class="menu-item menu-item--alt" style="top:793px"><h2 class="menu-item__name">Starter Sampler</h2><p class="menu-item__desc">Includes Mozza Sticks, Chicken Tenders, Onion Rings, and Chili Cheese Fries &nbsp;38</p></article>
    </section>

    <section class="dish-gallery">
      <figure class="dish" style="top:125px"><div class="dish__photo dish__photo--pizza" role="img" aria-label="Photo of cheesy bread slices arranged around a cup of marinara sauce"></div><figcaption class="dish__caption">Chili Cheese Fries</figcaption></figure>
      <figure class="dish" style="top:345px"><div class="dish__photo dish__photo--milanese" role="img" aria-label="Photo of breaded chicken cutlets with rice and green beans on a white plate"></div><figcaption class="dish__caption">Chicken Milanese</figcaption></figure>
      <figure class="dish" style="top:564px"><div class="dish__photo dish__photo--fries" role="img" aria-label="Photo of french fries topped with melted cheddar and beef chili"></div><figcaption class="dish__caption">Chili Cheese Fries</figcaption></figure>
      <figure class="dish" style="top:784px"><div class="dish__photo dish__photo--salad" role="img" aria-label="Photo of grilled halloumi salad with greens and tomatoes on a white plate"></div><figcaption class="dish__caption">Halloumi Salad</figcaption></figure>
    </section>
  </main>
</div>
</body>
</html>
```